Veltrane Group Business Card Design

The CEO is looking for a new trendy look for his business card.
You can stay with current branding or come up with something new/creative. It can be 3D, including Medical Office buildings. You can use our logo in a variety of colors. Please include name, title, company name, company website, email address, cell number

Target Market(s)

Real Estate Development and Construction

Industry/Entity Type

Health care real estate

Contact Information for Business Card

Rohesh Kamdar, CEO M-604.781.2249 E-roheshkamdar@veltrane.com Address:4180 Lindqvist Ave, Tampa, FL 33482 www.veltrane.com

Font styles to use
Other font styles liked:
• Be creative

Requirements
Must have
• Creative, trendy look
Nice to have
• Please go to our website to get a feel- www. veltrane.com
Should not have
• small fonts

```html
<!DOCTYPE html>
<html lang="en">
<head>
<meta charset="utf-8">
<title>Veltrane Group Business Card</title>
<link href="https://fonts.googleapis.com/css2?family=Montserrat:wght@300;400;700;800&display=swap" rel="stylesheet">
<style>
  :root {
    --navy: #1b3153;
    --red: #b01f29;
    --white: #ffffff;
    --backdrop: #2b2b2d;
  }
  * { margin: 0; padding: 0; box-sizing: border-box; }
  html, body {
    width: 1200px; height: 874px; overflow: hidden;
    background: var(--backdrop);
    font-family: "Montserrat", Arial, sans-serif;
  }
  .canvas { position: relative; width: 1200px; height: 874px; }
  .card {
    position: absolute; left: 320px; width: 560px; height: 320px;
    border-radius: 22px; overflow: hidden;
  }
  .card-front { top: 80px; background: var(--navy); }
  .card-back { top: 474px; background: var(--white); }

  .front-wordmark {
    position: absolute; left: 70px; top: 70px;
    color: var(--white); font-weight: 800; line-height: 0.95;
    font-size: 80px; letter-spacing: -2px;
  }
  .front-wordmark .sub { display: block; text-align: right; font-size: 48px; letter-spacing: 0; }

  .back-shapes { position: absolute; inset: 0; }

  .holder { position: absolute; left: 28px; top: 26px; color: var(--white); }
  .holder-name { font-weight: 700; font-size: 22px; letter-spacing: 0.5px; }
  .holder-title { font-weight: 300; font-size: 15px; margin-top: 2px; }

  .contact-list {
    position: absolute; left: 28px; top: 176px; list-style: none;
    color: var(--white); font-size: 14px; font-weight: 400; line-height: 1.5;
  }
  .contact-list li { display: flex; align-items: center; gap: 7px; }
  .contact-list .icon { width: 12px; height: 12px; flex: none; }

  .back-wordmark {
    position: absolute; right: 36px; top: 130px;
    color: var(--red); font-weight: 800; line-height: 0.95;
    font-size: 44px; letter-spacing: -1px; text-align: right;
  }
</style>
</head>
<body>
<main class="canvas">
  <section class="card card-front" aria-label="Card front">
    <p class="front-wordmark">Veltrane<span class="sub">Group</span></p>
  </section>

  <section class="card card-back" aria-label="Card back">
    <svg class="back-shapes" width="560" height="320" viewBox="0 0 560 320" aria-hidden="true">
      <defs>
        <clipPath id="left-panel">
          <path d="M0 0 H390 C320 0 300 100 275 150 C262 176 262 200 272 230 C290 285 320 320 370 320 H0 Z"/>
        </clipPath>
      </defs>
      <rect width="560" height="320" fill="var(--white)"/>
      <g clip-path="url(#left-panel)">
        <rect width="560" height="320" fill="var(--navy)"/>
        <rect width="560" height="150" fill="var(--red)"/>
        <rect x="0" y="150" width="560" height="3" fill="var(--white)"/>
      </g>
    </svg>

    <div class="holder">
      <p class="holder-name">ROHESH KAMDAR</p>
      <p class="holder-title">CEO</p>
    </div>

    <ul class="contact-list">
      <li>4180 Lindqvist Ave,</li>
      <li>Tampa, FL 33482</li>
      <li>
        <svg class="icon" viewBox="0 0 12 12"><rect x="3" y="0.5" width="6" height="11" rx="1.2" fill="none" stroke="var(--red)" stroke-width="1.4"/><circle cx="6" cy="9.3" r="0.8" fill="var(--red)"/></svg>
        604.781.2249
      </li>
      <li>
        <svg class="icon" viewBox="0 0 12 12"><rect x="0.5" y="2.5" width="11" height="7" fill="var(--red)"/><path d="M0.5 2.5 L6 6.5 L11.5 2.5" fill="none" stroke="var(--navy)" stroke-width="1"/></svg>
        roheshkamdar@veltrane.com
      </li>
      <li>
        <svg class="icon" viewBox="0 0 12 12"><circle cx="6" cy="6" r="5.2" fill="none" stroke="var(--red)" stroke-width="1.3"/><ellipse cx="6" cy="6" rx="2.2" ry="5.2" fill="none" stroke="var(--red)" stroke-width="1"/><path d="M1 6 H11" stroke="var(--red)" stroke-width="1"/></svg>
        www.veltrane.com
      </li>
    </ul>

    <p class="back-wordmark">Veltrane<br>Group</p>
  </section>
</main>
</body>
</html>
```